Professional Baby Bottle Bank Print Design

We need a baby bottle design that is 4.25" wide x 2.28" tall with a maximum of 6 colors (white is counted as a color).

The bottle design needs to be fun but professional. Bottles with cartoon images on it will be rejected immediately.

The bottle design wraps around the bottle. See examples here: https://vel.quin/cat/BabyBottles/HarlowBottles/5

Minimum font size is 10pt.

The bottle design must have the following text on it:
Main Text: Love them both
Paragraph text: Our ministry’s aim is to not only save unborn babies, but to provide love, support, and life-saving resources for vulnerable women in our community. By filling this bottle with cash, checks, and spare coins and returning it on collection day, you are truly saving and changing lives!
Optional text: Thank you!

We are including an example file and a template file. You do NOT have to use the template - but your file has to be the exact size mentioned. If you don't design as well as our sample, please don't waste our time by spamming us with hundreds of designs. We will ban design houses that spam us with designs that are more layouts (and not well designed).

Please note - white is a color. You don't have to do a box - but anything you don't make white will be see-through.

We will take the winners of this contest to a survey with the customers. We may choose two and edit the text of one slightly to be different. We must know the fonts used.

No gradients unless they are half-toned with relatively big sized dots.

Target Market(s)

Church Attendees coming from a Pregnancy Center

Industry/Entity Type

Religious Christian Churches

Requirements
Must have
• Professional, great palette, wording as described.
Nice to have
• Integrated design across the whole space with areas for text (no text all the way across)
Should not have
• Cartoon figures; elements shoved together that don't go together (i.e. - actually design something)

```html
<!DOCTYPE html>
<html lang="en">
<head>
<meta charset="utf-8">
<title>Love Them Both – Baby Bottle Label</title>
<link href="https://fonts.googleapis.com/css2?family=Abril+Fatface&family=PT+Sans+Narrow&family=Kaushan+Script&display=swap" rel="stylesheet">
<style>
  :root {
    --page-bg: #fbdbe9;
    --label-white: #ffffff;
    --label-mist: #eeeff3;
    --love-red: #e8466b;
    --sky-blue: #1a9fdb;
    --body-grey: #545454;
    --photo-pink: #f1d3dc;
    --photo-skin: #e9b9a4;
    --star-blue: #cfe7f6;
    --star-yellow: #f8e6ae;
    --star-pink: #f5cfe0;
  }
  html, body {
    margin: 0;
    width: 1200px;
    height: 1200px;
    overflow: hidden;
    background: var(--page-bg);
  }
  .bottle-label {
    position: absolute;
    left: 50px;
    top: 305px;
    width: 1100px;
    height: 590px;
    background: linear-gradient(90deg, var(--label-mist) 0%, var(--label-white) 45%, var(--label-white) 80%, var(--label-mist) 100%);
    overflow: hidden;
  }
  .hands-photo {
    position: absolute;
    left: 0;
    top: 0;
    width: 440px;
    height: 590px;
    background:
      radial-gradient(ellipse 55% 40% at 55% 62%, var(--photo-skin) 0%, rgba(233,185,164,0) 100%),
      linear-gradient(90deg, var(--photo-pink) 0%, #f2e7ec 70%, rgba(255,255,255,0) 100%);
  }
  .soft-star {
    position: absolute;
    border-radius: 50%;
  }
  .soft-star.blue { left: 932px; top: 36px; width: 140px; height: 140px; background: radial-gradient(circle, var(--star-blue) 55%, rgba(207,231,246,0) 72%); }
  .soft-star.yellow { left: 927px; top: 451px; width: 82px; height: 82px; background: radial-gradient(circle, var(--star-yellow) 55%, rgba(248,230,174,0) 72%); }
  .soft-star.pink { left: 35px; top: 462px; width: 92px; height: 92px; background: radial-gradient(circle, var(--star-pink) 55%, rgba(245,207,224,0) 72%); }
  .blossom { position: absolute; border-radius: 50%; background: var(--star-pink); }
  .headline {
    position: absolute;
    left: 468px;
    top: 52px;
    margin: 0;
    font-family: 'Abril Fatface', serif;
    font-weight: 400;
    line-height: 1;
  }
  .headline .love { display: block; color: var(--love-red); font-size: 96px; letter-spacing: 1px; }
  .headline .them-both { display: block; color: var(--sky-blue); font-size: 56px; margin-top: 2px; margin-left: 4px; letter-spacing: 1px; }
  .mission {
    position: absolute;
    left: 477px;
    top: 244px;
    width: 590px;
    margin: 0;
    font-family: 'PT Sans Narrow', sans-serif;
    font-size: 27px;
    line-height: 39px;
    color: var(--body-grey);
    text-indent: 16px;
  }
  .thanks {
    position: absolute;
    left: 615px;
    top: 450px;
    margin: 0;
    font-family: 'Kaushan Script', cursive;
    font-size: 42px;
    color: var(--sky-blue);
  }
</style>
</head>
<body>
  <div class="bottle-label">
    <div class="hands-photo" role="img" aria-label="Photo of an adult hand gently holding a newborn's hand on a soft pink blanket"></div>
    <div class="blossom" role="img" aria-label="Small pink flower decoration" style="left:35px;top:35px;width:34px;height:34px;"></div>
    <div class="blossom" role="img" aria-label="Small pink flower decoration" style="left:107px;top:49px;width:18px;height:18px;"></div>
    <div class="blossom" role="img" aria-label="Small pink flower decoration" style="left:382px;top:78px;width:44px;height:44px;"></div>
    <div class="soft-star pink" role="img" aria-label="Soft pink star balloon decoration"></div>
    <div class="soft-star blue" role="img" aria-label="Soft blue star balloon decoration"></div>
    <div class="soft-star yellow" role="img" aria-label="Soft yellow star balloon decoration"></div>

    <h1 class="headline">
      <span class="love">Love</span>
      <span class="them-both">them both</span>
    </h1>
    <p class="mission">Our ministry’s aim is to not only save unborn babies, but to provide love, support, and life-saving resources for vulnerable women in our community. By filling this bottle with cash, checks, and spare coins and returning it on collection day, you are truly saving and changing lives!</p>
    <p class="thanks">Thank you!</p>
  </div>
</body>
</html>
```